Product Design for VelaMira

Design Brief for VelaMira Product Packaging

Objective:
Create a cohesive, elegant, and brand-consistent packaging design for the VelaMira product line. The signature visual theme should reflect luxury, femininity, and clean beauty values.

---

🎨 Core Design Direction

Unified Aesthetic: All containers must prominently feature the floral pattern shown in "Pattern Reference: Image 3". This design serves as the brand's signature aesthetic and must be applied uniformly across all SKUs.

Brand Logo Placement: The VelaMira logo (provided) should be clearly visible and harmoniously integrated into the patterned background.

Color Palette: Base colors should complement the brand’s primary palette: black, blush pink, and white.

---

🧴 Product-Specific Packaging Specifications

1. Mascara

Bottle Type: Sleek mascara tube with a wand applicator

Capacity: 5ml

Design: Use floral pattern from Pattern Reference Image 3. Ensure the pattern does not obstruct the readability of the logo or any regulatory text.

2. Eyebrow Growth Serum

Bottle Type: 5ml tube with fine-tip brush applicator

Capacity: 5ml

Design: Same floral pattern, scaled and applied proportionally to match the mascara for consistency

3. Eyelash Growth Serum

Bottle Type: 5ml tube with fine-tip brush (similar to the eyebrow serum, unless otherwise advised)

Capacity: 5ml

Design: Identical styling to maintain unity across lash & brow products

4. Anti-Aging Serum or Lotion

Bottle Type: 30ml airless pump bottle (preferred for hygiene and product stability)

Capacity: 30ml

Design: Apply floral pattern from Pattern Reference and scale appropriately for larger surface area

5. Hair Growth Spray

Bottle Type: 50ml fine mist spray bottle

Capacity: 50ml

Design: Pattern applied and scaled for taller profile; maintain visual harmony with skincare line

---

📦 Additional Notes

Please ensure packaging aligns with clean beauty standards (no overly glossy plastic finishes, avoid excessive secondary packaging unless sustainable).

Materials should be eco-conscious where possible.

If embossing, foil stamping, or UV finishing is available for logo accents, please suggest options.

```html
<!DOCTYPE html>
<html lang="en">
<head>
<meta charset="UTF-8">
<title>VelaMira Anti-Aging Face Serum Label</title>
<link rel="stylesheet" href="https://fonts.googleapis.com/css2?family=Lato:wght@400;700&family=Playfair+Display:wght@400&display=swap">
<style>
  :root {
    --backdrop: #e5e6e6;
    --panel-black: #0c0c0c;
    --cream: #efe4d4;
    --copper: #c7743d;
    --pattern-light: #fbf3ec;
    --pattern-mid: #f0d3bc;
  }
  * { box-sizing: border-box; margin: 0; padding: 0; }
  html, body { width: 1200px; height: 1200px; overflow: hidden; }
  body {
    background: var(--backdrop);
    font-family: "Lato", sans-serif;
    color: var(--cream);
    position: relative;
  }
  .label-sheet {
    position: absolute;
    left: 50px; top: 311px;
    width: 1100px; height: 577px;
  }
  .floral-pattern {
    position: absolute; inset: 0;
    background:
      radial-gradient(circle at 20% 30%, var(--pattern-mid) 0, transparent 22%),
      radial-gradient(circle at 55% 70%, var(--pattern-mid) 0, transparent 20%),
      radial-gradient(circle at 85% 25%, var(--pattern-mid) 0, transparent 22%),
      linear-gradient(135deg, var(--pattern-light), #f6e2d2);
  }
  .panel {
    position: absolute;
    top: 103px; width: 299px; height: 373px;
    background: var(--panel-black);
    display: flex; flex-direction: column; align-items: center;
    text-align: center;
  }
  .panel--front { left: 125px; padding-top: 62px; }
  .panel--back { left: 674px; padding: 26px 14px 0; }
  .brand-name {
    font-family: "Playfair Display", serif;
    font-size: 50px; line-height: 1;
    color: var(--cream);
  }
  .product-title {
    margin-top: 60px;
    font-weight: 700; font-size: 23px; line-height: 1.15;
  }
  .product-benefits { margin-top: 14px; font-size: 16px; }
  .product-volume { margin-top: 44px; font-size: 17px; }
  .info-heading { font-weight: 700; font-size: 15px; line-height: 1.3; }
  .info-text { font-size: 14.5px; line-height: 1.35; }
  .info-block { margin-bottom: 10px; }
  .info-caution { font-size: 14.5px; }
  .info-caution strong { font-weight: 700; margin-right: 4px; }
  .claim-row { display: flex; gap: 14px; margin-top: 18px; }
  .claim { width: 48px; display: flex; flex-direction: column; align-items: center; }
  .claim svg { width: 36px; height: 36px; }
  .claim-label {
    margin-top: 3px; font-size: 8px; font-weight: 700; line-height: 1.15;
    color: var(--copper);
  }
  .distributor { margin-top: 16px; font-size: 14.5px; line-height: 1.4; }
  .distributor strong { font-weight: 700; }
</style>
</head>
<body>
  <main class="label-sheet">
    <div class="floral-pattern" role="img" aria-label="Repeating floral pattern of copper-toned hand-drawn blossoms and leaves on white"></div>

    <section class="panel panel--front">
      <h1 class="brand-name">VelaMira</h1>
      <h2 class="product-title">Anti-Aging Face<br>Serum</h2>
      <p class="product-benefits">Hydrates • Firms • Brightens</p>
      <p class="product-volume">30ml / 1.0 fl.oz.</p>
    </section>

    <section class="panel panel--back">
      <div class="info-block">
        <p class="info-heading">Directions:</p>
        <p class="info-text">Apply 1–2 pumps to clean, dry<br>skin. Use AM &amp; PM.</p>
      </div>
      <div class="info-block">
        <p class="info-heading">Directions:</p>
        <p class="info-text">Aqua, Hyaluronic Acid,<br>Niacinamide, Retinol...</p>
      </div>
      <p class="info-caution"><strong>Caution:</strong>For external use only.</p>

      <div class="claim-row">
        <div class="claim">
          <svg viewBox="0 0 36 36" fill="none" stroke="var(--copper)" stroke-width="1.6">
            <circle cx="18" cy="18" r="16"/>
            <path d="M15 10h6M16 10v6l-5 9h14l-5-9v-6"/>
            <path d="M8 8l20 20"/>
          </svg>
          <span class="claim-label">Paraben Free</span>
        </div>
        <div class="claim">
          <svg viewBox="0 0 36 36" fill="none" stroke="var(--copper)" stroke-width="1.6">
            <circle cx="18" cy="18" r="16"/>
            <path d="M11 18l5 5 9-10"/>
          </svg>
          <span class="claim-label">Dermatologist Tested</span>
        </div>
        <div class="claim">
          <svg viewBox="0 0 36 36" fill="none" stroke="var(--copper)" stroke-width="1.6">
            <circle cx="18" cy="18" r="16"/>
            <path d="M18 9c4 6 6 9 6 12a6 6 0 0 1-12 0c0-3 2-6 6-12z"/>
          </svg>
          <span class="claim-label">Cruelty Free</span>
        </div>
        <div class="claim">
          <svg viewBox="0 0 36 36" fill="none" stroke="var(--copper)" stroke-width="1.6">
            <circle cx="18" cy="18" r="16"/>
            <path d="M18 9c6 4 7 10 0 17c-7-7-6-13 0-17zM18 13v15"/>
          </svg>
          <span class="claim-label">Strengthens Roots</span>
        </div>
      </div>

      <p class="distributor">Distributed by: <strong>VelaMira</strong>,<br>London, UK</p>
    </section>
  </main>
</body>
</html>
```